Hueverberant (Synth Presets Expansion Pack)

Hello Designers! I'm an audio engineer and beat maker who is about to start selling sound packs on my website www.brindlemoorstudio.com. I'm looking to have some art created for my new QUARTZEN Preset Bank called "Hueverberant". QUARTZEN is a Synth from Pellow Acoustics if you want to learn more about it. Hueverberant is a sub type of synthesthesia, a syndrome where people see colors when they hear sounds. Check out this video to learn more https://www.vidlorn.com/watch?v=kq7TzwPmd3X
I've attached some examples of another producers sound pack graphics and boxes, so you have an idea of what I'm looking for. I also have attached two pictures of "Hueverberant" to inspire the graphics I'm hoping for on my new product. I would like my product to say "www.BrindleMoorStudio.com Presents" at the top. At the bottom I would like my logo to go on the bottom left. Please also add the Lumo and KT logo on the bottom right. If you have any questions please let me know.

Target Market(s)

97% of my customers are upcoming producers, 18-45 years old, and are guys.

Industry/Entity Type

Audio

Requirements
Must have
• What I asked for in the description.

```html
<!DOCTYPE html>
<html lang="en">
<head>
<meta charset="utf-8">
<title>Hueverberant – Synth Preset Bank Cover</title>
<link rel="stylesheet" href="https://fonts.googleapis.com/css2?family=Michroma&family=Share+Tech+Mono&display=swap">
<style>
  :root{
    --stage:#4a4a4a;
    --cover-dark:#161616;
    --cover-texture:#2a2a2a;
    --panel:#262626;
    --cyan:#14c4e6;
    --cyan-deep:#0a9bbd;
    --white:#f4f4f4;
    --muted:#bdbdbd;
  }
  html,body{margin:0;padding:0;overflow:hidden;}
  body{
    width:1200px;height:1200px;
    background:radial-gradient(ellipse at 50% 60%, #5a5a5a 0%, var(--stage) 70%);
    position:relative;
  }
  .cover{
    position:absolute;left:258px;top:30px;
    width:684px;height:1140px;
    overflow:hidden;
    background:
      radial-gradient(ellipse at 40% 55%, var(--cover-texture) 0%, var(--cover-dark) 75%);
    box-shadow:0 20px 60px rgba(0,0,0,.5);
  }
  .presenter{
    position:absolute;top:118px;left:0;right:0;
    text-align:center;
    font-family:"Share Tech Mono", monospace;
  }
  .presenter__url{
    color:var(--white);font-size:24px;letter-spacing:2px;
  }
  .presenter__label{
    color:var(--cyan);font-size:19px;letter-spacing:13px;margin-top:6px;
  }
  .art-colour-cloud{
    position:absolute;left:0;top:230px;width:500px;height:420px;
    border-radius:0 55% 45% 0 / 0 50% 60% 0;
    background:linear-gradient(120deg,#7b5bd6 0%,#b45fd0 30%,#4f7fd8 55%,#3fa59a 75%,#c7a24a 100%);
    opacity:.75;
    filter:blur(6px);
  }
  .art-listener{
    position:absolute;right:0;top:190px;width:280px;height:700px;
    background:linear-gradient(100deg,rgba(30,30,30,0) 0%,#5a5a5a 45%,#8a8a8a 75%,#4a4a4a 100%);
  }
  .swoosh{position:absolute;left:0;top:0;width:684px;height:1140px;}
  .title{
    position:absolute;left:0;right:0;top:1008px;
    text-align:center;
    font-family:"Michroma", sans-serif;
    font-size:52px;letter-spacing:2px;
    color:var(--white);
    margin:0;font-weight:400;
  }
  .title{top:895px;}
  .studio-mark{
    position:absolute;left:48px;bottom:56px;
    display:flex;align-items:center;gap:12px;
    font-family:"Michroma", sans-serif;font-size:19px;color:var(--white);
  }
  .studio-mark__square{width:26px;height:26px;background:var(--cyan);}
  .platforms{
    position:absolute;right:42px;bottom:100px;
    display:flex;gap:26px;
    font-family:"Michroma", sans-serif;font-size:26px;color:var(--cyan);
  }
</style>
</head>
<body>
  <main class="cover">
    <div class="art-colour-cloud" role="img" aria-label="Cloud of overlapping translucent coloured bokeh circles flowing from the listener's headphones"></div>
    <div class="art-listener" role="img" aria-label="Black and white photograph of a woman wearing headphones, eyes closed, with small coloured dots at her eyes"></div>

    <header class="presenter">
      <div class="presenter__url">WWW.BRINDLEMOORSTUDIO.COM</div>
      <div class="presenter__label">PRESENTS</div>
    </header>

    <svg class="swoosh" viewBox="0 0 684 1140" aria-hidden="true">
      <defs>
        <linearGradient id="swooshGradient" x1="0" y1="0" x2="1" y2="0">
          <stop offset="0" stop-color="#0a9bbd"/>
          <stop offset="0.5" stop-color="#18d4f2"/>
          <stop offset="1" stop-color="#0a9bbd"/>
        </linearGradient>
      </defs>
      <path d="M0 895 C 200 815, 500 830, 684 660 L684 1140 L0 1140 Z" fill="var(--panel)"/>
      <path d="M0 850 C 200 778, 500 805, 684 636 L684 660 C 500 830, 200 815, 0 895 Z" fill="url(#swooshGradient)"/>
    </svg>

    <h1 class="title">HUEVERBERANT</h1>

    <div class="studio-mark">
      <span class="studio-mark__square"></span>
      <span>BrindleMoorStudio</span>
    </div>

    <div class="platforms">
      <span>KT</span>
      <span>Lumo</span>
    </div>
  </main>
</body>
</html>
```